Business Card For Halvenmoor Financial Consulting

Hi, I would like a business card designed. Bold, modern.
Please use the same design as the logo. I have also attached the website design to see the overall theme.
Wordmark Font
Color: Hex: #01AEF7

```html
<!DOCTYPE html>
<html lang="en">
<head>
<meta charset="utf-8">
<title>Halvenmoor Financial Consulting — Business Card</title>
<link rel="stylesheet" href="https://fonts.googleapis.com/css2?family=Montserrat:wght@600;700&family=Lato:wght@400;700&display=swap">
<style>
  :root {
    --backdrop: #6e6c6a;
    --card: #0f161e;
    --brand-blue: #01aef7;
    --white: #ffffff;
    --soft-white: #eef0f2;
  }
  * { box-sizing: border-box; margin: 0; padding: 0; }
  html, body { width: 1200px; height: 911px; overflow: hidden; }
  body {
    background: var(--backdrop);
    position: relative;
    font-family: "Lato", Arial, sans-serif;
  }
  .card {
    position: absolute;
    top: 301px;
    width: 540px;
    height: 309px;
    background: var(--card);
    overflow: hidden;
    box-shadow: 0 14px 30px rgba(0,0,0,0.35);
  }
  .card--front { left: 40px; }
  .card--back { left: 620px; }

  /* Front */
  .brand {
    position: absolute;
    left: 0; right: 0; top: 0; bottom: 0;
    display: flex;
    align-items: center;
    justify-content: center;
    gap: 16px;
  }
  .brand__square {
    width: 34px; height: 34px;
    border: 4px solid var(--brand-blue);
    flex: none;
  }
  .brand__name {
    font-family: "Montserrat", Arial, sans-serif;
    font-weight: 700;
    font-size: 23px;
    letter-spacing: 1px;
    color: var(--white);
    text-transform: uppercase;
    line-height: 1.15;
  }

  /* Back */
  .back-bands { position: absolute; inset: 0; }
  .mark {
    position: absolute;
    left: 50px; top: 96px;
    width: 170px; height: 170px;
    border: 12px solid var(--brand-blue);
    display: flex;
    align-items: center;
    justify-content: center;
    text-align: center;
    padding: 8px;
  }
  .mark__name {
    font-family: "Montserrat", Arial, sans-serif;
    font-weight: 700;
    font-size: 15px;
    color: var(--white);
    text-transform: uppercase;
    line-height: 1.3;
  }
  .contact {
    position: absolute;
    left: 262px; top: 62px;
    color: var(--soft-white);
  }
  .contact__name {
    font-family: "Montserrat", Arial, sans-serif;
    font-weight: 700;
    font-size: 22px;
    color: var(--white);
    text-transform: uppercase;
    letter-spacing: 0.3px;
  }
  .contact__role {
    font-size: 15px;
    color: var(--brand-blue);
    margin-bottom: 14px;
  }
  .contact__list { list-style: none; }
  .contact__item {
    display: flex;
    align-items: flex-start;
    gap: 10px;
    font-size: 12.5px;
    line-height: 1.4;
    margin-bottom: 5px;
  }
  .contact__icon { width: 12px; height: 12px; flex: none; margin-top: 3px; }
</style>
</head>
<body>

<section class="card card--front" aria-label="Business card front">
  <div class="brand">
    <span class="brand__square"></span>
    <span class="brand__name">Halvenmoor<br>Financial Consulting</span>
  </div>
</section>

<section class="card card--back" aria-label="Business card back">
  <svg class="back-bands" viewBox="0 0 540 309" width="540" height="309" aria-hidden="true">
    <polygon points="0,0 200,0 176,22 0,22" fill="var(--white)"/>
    <polygon points="0,0 0,0 0,0" fill="none"/>
    <polygon points="300,309 330,284 540,284 540,309" fill="var(--brand-blue)"/>
  </svg>

  <div class="mark">
    <span class="mark__name">Halvenmoor Financial Consulting</span>
  </div>

  <div class="contact">
    <h1 class="contact__name">Daniel Reyes</h1>
    <p class="contact__role">Founder &amp; CEO</p>
    <ul class="contact__list">
      <li class="contact__item">
        <svg class="contact__icon" viewBox="0 0 12 12"><path d="M6 0.5a4 4 0 0 0-4 4c0 3 4 7 4 7s4-4 4-7a4 4 0 0 0-4-4zm0 5.5a1.5 1.5 0 1 1 0-3 1.5 1.5 0 0 1 0 3z" fill="var(--brand-blue)"/></svg>
        <span>Your Address, City<br>State, Zip 1235</span>
      </li>
      <li class="contact__item">
        <svg class="contact__icon" viewBox="0 0 12 12"><path d="M2.5 1 L4.5 1 L5.3 3.6 L4 4.6 C4.7 6 6 7.3 7.4 8 L8.4 6.7 L11 7.5 L11 9.5 C11 10.3 10.3 11 9.5 11 C5 11 1 7 1 2.5 C1 1.7 1.7 1 2.5 1 Z" fill="var(--brand-blue)"/></svg>
        <span>(123) 456-7890</span>
      </li>
      <li class="contact__item">
        <svg class="contact__icon" viewBox="0 0 12 12"><rect x="3" y="0.5" width="6" height="11" rx="1" fill="none" stroke="var(--brand-blue)" stroke-width="1.4"/><circle cx="6" cy="9.5" r="0.8" fill="var(--brand-blue)"/></svg>
        <span>(231) 456-7890</span>
      </li>
      <li class="contact__item">
        <svg class="contact__icon" viewBox="0 0 12 12"><rect x="0.5" y="2" width="11" height="8" fill="var(--brand-blue)"/><path d="M0.5 2 L6 6.5 L11.5 2" fill="none" stroke="var(--card)" stroke-width="1"/></svg>
        <span>info@halvenmoorconsulting.com</span>
      </li>
      <li class="contact__item">
        <svg class="contact__icon" viewBox="0 0 12 12"><circle cx="6" cy="6" r="5" fill="none" stroke="var(--brand-blue)" stroke-width="1.3"/><path d="M1 6 H11 M6 1 C3.5 4 3.5 8 6 11 C8.5 8 8.5 4 6 1" fill="none" stroke="var(--brand-blue)" stroke-width="1"/></svg>
        <span>halvenmoorconsulting.com</span>
      </li>
    </ul>
  </div>
</section>

</body>
</html>
```